Barrister at Law needs Business Card Design

Need a business card design for Barrister at Law. Double sided. Simple Neil Thorsby and Barrister at Law on one side with contact details on the other side. I would like a professional design using Black or Platinum. Details on reverse side would include qualifications - Bcom-Llb and Acc Spec Commercial Litigation. I have attached the logo. Contact details would include address/ Po Box/ Phone/Fax/Mobile/email. I would like to use raised print or spot gloss.

```html
<!DOCTYPE html>
<html lang="en">
<head>
<meta charset="utf-8">
<title>Neil Thorsby – Barrister-at-Law Business Card</title>
<link href="https://fonts.googleapis.com/css2?family=Cinzel:wght@400;500&family=Nunito+Sans:wght@400&display=swap" rel="stylesheet">
<style>
  :root {
    --backdrop: #6e5443;
    --card: #2a2a2c;
    --accent-blue: #1f78c1;
    --title-grey: #a8a8aa;
    --text-grey: #b4b4b6;
    --mark-tone: #3a3a3d;
  }
  * { margin: 0; padding: 0; box-sizing: border-box; }
  html, body { width: 1200px; height: 1000px; overflow: hidden; }
  body { background: var(--backdrop); position: relative; font-family: "Nunito Sans", sans-serif; }

  .card {
    position: absolute;
    left: 265px;
    width: 666px;
    height: 397px;
    background: var(--card);
    border-radius: 24px;
  }
  .card--contact { top: 73px; }
  .card--name { top: 533px; }

  .name {
    font-family: "Cinzel", serif;
    font-weight: 500;
    color: var(--accent-blue);
    white-space: nowrap;
  }
  .role {
    font-family: "Cinzel", serif;
    color: var(--title-grey);
    white-space: nowrap;
  }

  /* Contact side */
  .card--contact .name { position: absolute; left: 51px; top: 38px; font-size: 33px; letter-spacing: 0.5px; }
  .card--contact .role { position: absolute; left: 52px; top: 78px; font-size: 19px; letter-spacing: 4.2px; }
  .qualification { position: absolute; left: 52px; top: 122px; font-size: 15px; color: var(--text-grey); }
  .address { position: absolute; left: 52px; top: 208px; font-size: 15.5px; line-height: 24px; color: var(--text-grey); }
  .contact-list { position: absolute; left: 52px; top: 266px; list-style: none; }
  .contact-list li { display: flex; align-items: center; height: 23.8px; font-size: 15.5px; color: var(--text-grey); }
  .contact-list svg { width: 13px; height: 13px; margin-right: 8px; fill: var(--accent-blue); }

  .chambers-mark {
    position: absolute;
    left: 410px;
    top: 180px;
    width: 210px;
    text-align: center;
    font-family: "Cinzel", serif;
    font-size: 24px;
    line-height: 32px;
    color: var(--mark-tone);
  }

  /* Name side */
  .card--name .name { position: absolute; left: 0; width: 100%; text-align: center; top: 152px; font-size: 47px; letter-spacing: 1px; }
  .card--name .role { position: absolute; left: 0; width: 100%; text-align: center; top: 208px; font-size: 27px; letter-spacing: 6.5px; }
  .specialty { position: absolute; left: 0; width: 100%; text-align: center; top: 336px; font-size: 16.5px; letter-spacing: 0.6px; color: var(--text-grey); }
</style>
</head>
<body>

<section class="card card--contact">
  <h1 class="name">NEIL THORSBY</h1>
  <p class="role">BARRISTER-AT-LAW</p>
  <p class="qualification">LLB Acc. Spec. (Fam.)</p>
  <p class="address">Unit 4/58 Kestrel Lane<br>BRISBANE Qld 4000</p>
  <ul class="contact-list">
    <li>
      <svg viewBox="0 0 16 16"><path d="M4 0h8a1 1 0 0 1 1 1v14a1 1 0 0 1-1 1H4a1 1 0 0 1-1-1V1a1 1 0 0 1 1-1zm.5 1.5v11h7v-11zM8 13.5a.8.8 0 1 0 0 1.6.8.8 0 0 0 0-1.6z"/></svg>
      + 000 000 0000
    </li>
    <li>
      <svg viewBox="0 0 16 16"><path d="M1 6c0-2 3-3 7-3s7 1 7 3v1h-3.5V5.5h-7V7H1zM3.5 8h9l1.5 6H2z"/></svg>
      + 000 000 0000
    </li>
    <li>
      <svg viewBox="0 0 16 16"><path d="M4 1h8v4H4zM1 6h14v6h-2.5v-2h-9v2H1zM4.5 11h7v4h-7z"/></svg>
      + 000 000 0000
    </li>
    <li>
      <svg viewBox="0 0 16 16"><path d="M1 3h14v1.2L8 9 1 4.2zM1 5.8l7 4.8 7-4.8V13H1z"/></svg>
      info@thorsbychambers.com
    </li>
  </ul>
  <p class="chambers-mark">Thorsby<br>Chambers</p>
</section>

<section class="card card--name">
  <h2 class="name">NEIL THORSBY</h2>
  <p class="role">BARRISTER-AT-LAW</p>
  <p class="specialty">Bcom-Llb and Acc Spec Commercial Litigation</p>
</section>

</body>
</html>
```